The Polish & Glow Studio Website Update

Hello. I am seeking to freshen up my website with a clean and easy feel that incorporates our modern chic style. Our services cater to mostly young professionals and modern moms.

We focus on natural nail care and gentle professional waxing. We are known for our cleanliness. Our clients like our current website, however I'm hoping to make it look even more professional and user friendly. Some clients have even said our current website feels welcoming, unlike other websites that in they feel give a snobbish vibe. I like clean lines, simple, fresh, and sometimes bold. Totally NOT a fan of whimsical.

I threw added an accent color to the color pallet...however it should be used in moderation. I am also open to other accent colors. I'd like the site to emphasize the Brazilian wax as much as nails, if not more than nail. The photos downloaded are just to give you a few images of who we are, however are not necessary. Current website www.thepolishandglowstudio.example

Target Market(s)

Females 30-55

Industry/Entity Type

Beauty Salon

Coding

Coded - Design and coding required

Number of Pages Required

5+ page

Font styles to use
Sans Serif

Colors
ffffff
1b1b1b
acd136
eeeeee
878787
c4c4c4
efefef
7f7f7f

Requirements
Must have
• Clean look
Nice to have
• Our logo
Should not have
• Whimsical

```html
<!DOCTYPE html>
<html lang="en">
<head>
<meta charset="utf-8">
<title>The Polish &amp; Glow Studio</title>
<link href="https://fonts.googleapis.com/css2?family=Roboto:wght@300;400;500&display=swap" rel="stylesheet">
<style>
:root{
  --green:#acd136;
  --dark:#1b1b1b;
  --navy:#0e1621;
  --grey:#878787;
  --line:#e3e3e3;
  --light:#efefef;
  --yellow:#f0bb3f;
  --teal:#00a99d;
  --pink:#d6679a;
  --sage:#b2cb78;
  --white:#ffffff;
}
*{margin:0;padding:0;box-sizing:border-box}
html,body{width:752px;height:1200px;overflow:hidden}
body{position:relative;font-family:'Roboto',sans-serif;color:var(--dark);background:var(--white)}
.abs{position:absolute}
.brand{left:62px;top:30px;display:flex;align-items:center;gap:6px;font-size:17px;font-weight:400;color:var(--dark);letter-spacing:.2px}
.brand-dot{width:10px;height:10px;border-radius:50%;background:var(--green)}
.contact{top:18px;font-size:7.5px;color:#555;display:flex;align-items:center;gap:4px}
.search{left:526px;top:42px;width:165px;height:28px;border:1px solid #c4c4c4;border-radius:3px;font-size:7px;color:#999;padding:10px 10px;box-shadow:0 1px 2px rgba(0,0,0,.1)}
.search svg{position:absolute;right:8px;top:7px}
.nav{left:0;top:83px;width:752px;height:52px;background:var(--green)}
.nav ul{list-style:none;position:absolute;left:62px;top:0;display:flex;height:52px}
.nav li{font-size:8px;color:var(--white);line-height:52px;padding:0 14.8px;text-transform:uppercase}
.nav li.active{background:var(--dark);padding:0 16px}
.hero{left:0;top:135px;width:752px;height:363px;background:radial-gradient(ellipse at 50% 35%,#6b5a52 0%,#4a403c 45%,#3a3432 100%)}
.hero h1{position:absolute;left:0;width:752px;top:164px;text-align:center;color:var(--white);font-size:19.5px;font-weight:400;line-height:24px}
.hero-arrow{top:162px;width:26px;height:26px;border:1.5px solid rgba(255,255,255,.35);border-radius:50%}
.cta{left:311px;top:228px;width:130px;height:35px;background:var(--green);display:flex;color:var(--white);font-size:9.5px;font-weight:500}
.cta span{flex:1;line-height:35px;padding-left:10px}
.cta i{width:35px;background:#9bbd2c;display:flex;align-items:center;justify-content:center}
.card{top:430px;width:152px;height:216px;background:var(--white);border:1px solid #dedede}
.card-top{height:70px;display:flex;align-items:center;justify-content:center}
.card h3{font-size:11px;font-weight:400;text-align:center;margin:16px 9px 0;padding-bottom:10px;border-bottom:1px solid var(--line)}
.card p{font-size:6.8px;font-weight:300;color:var(--grey);line-height:12.8px;margin:12px 8px 0;text-align:justify}
.card-more{position:absolute;right:-1px;bottom:-1px;width:25px;height:25px;background:#9a9a9a}
.card-more.on{background:var(--teal)}
.card-more svg{margin:8px}
.btn{background:var(--green);color:var(--white);display:flex;align-items:center;justify-content:center}
.view{left:299px;top:672px;width:154px;height:37px;font-size:11px}
.mission-photo{left:62px;top:735px;width:311px;height:201px;border:2px solid var(--light);background:linear-gradient(135deg,#d8ccc0 0%,#c49a88 45%,#e2b7a4 70%,#cfc2b6 100%)}
.mission{left:393px;top:733px;width:297px}
.mission h2{font-size:13px;font-weight:400;margin-bottom:9px}
.mission p{font-size:6.8px;line-height:12.8px;color:#555;text-align:justify;margin-bottom:13px}
.readmore{left:393px;top:911px;width:68px;height:24px;font-size:6.8px;font-weight:500}
.footer{left:0;top:968px;width:752px;height:232px;background:var(--navy)}
.zigzag{left:0;top:966px;width:752px;height:10px;background:linear-gradient(135deg,var(--white) 25%,transparent 25%) -5px 0,linear-gradient(225deg,var(--white) 25%,transparent 25%) -5px 0;background-size:10px 10px}
.fcol{top:1005px;color:var(--white)}
.fcol h4{font-size:13px;font-weight:400;margin-bottom:15px;padding-left:1px}
.fcol ul{list-style:none;width:107px}
.fcol li{font-size:7px;height:19.3px;line-height:19px;border-bottom:1px solid #1f2a37;position:relative}
.fcol li:last-child{border-bottom:none}
.fcol li.go::after{content:"»";position:absolute;right:0;color:var(--green);font-size:9px}
.news p{font-size:7px;line-height:12px;width:132px;margin-bottom:11px;color:#dde}
.news .email{width:131px;height:26px;background:var(--white);font-size:7.5px;color:#999;padding:8px 7px}
.subscribe{left:624px;top:1107px;width:67px;height:26px;font-size:7.5px}
.copy{left:63px;top:1169px;font-size:7.5px;color:#7f7f7f}
</style>
</head>
<body>

<header>
  <div class="abs brand"><span class="brand-dot"></span>The Polish &amp; Glow Studio</div>
  <div class="abs contact" style="left:459px">
    <svg width="6" height="8" viewBox="0 0 6 8"><path d="M3 0a3 3 0 0 0-3 3c0 2 3 5 3 5s3-3 3-5a3 3 0 0 0-3-3z" fill="#acd136"/></svg>
    42 Linden Avenue, Brookhaven, CT 06590
  </div>
  <div class="abs contact" style="left:615px">
    <svg width="7" height="7" viewBox="0 0 7 7"><rect width="7" height="7" rx="1.5" fill="#acd136"/></svg>
    ph: (203) 555-0147
  </div>
  <div class="abs search">Search...
    <svg width="11" height="11" viewBox="0 0 11 11"><circle cx="4.5" cy="4.5" r="3.5" fill="none" stroke="#777" stroke-width="1.4"/><path d="M7 7l3 3" stroke="#777" stroke-width="1.6"/></svg>
  </div>
</header>

<nav class="abs nav">
  <ul>
    <li class="active">Home</li>
    <li>Schedule an appointment</li>
    <li>Products and services</li>
    <li>Careers</li>
    <li>Specials</li>
    <li>About us</li>
    <li>FAQ</li>
    <li>Contact us</li>
  </ul>
</nav>

<section class="abs hero" role="img" aria-label="Close-up photo of manicured hands">
  <div class="abs hero-arrow" style="left:35px"></div>
  <div class="abs hero-arrow" style="left:691px"></div>
  <h1>FACIALS ARE NOW AVAILABLE AT<br>THE POLISH &amp; GLOW STUDIO</h1>
  <div class="abs cta"><span>APPOINMENT</span><i>
    <svg width="18" height="18" viewBox="0 0 18 18" fill="#fff"><circle cx="7" cy="7" r="5"/><circle cx="13" cy="13" r="3.5"/><circle cx="7" cy="7" r="2" fill="#9bbd2c"/><circle cx="13" cy="13" r="1.3" fill="#9bbd2c"/></svg>
  </i></div>
</section>

<section class="services">
  <article class="abs card" style="left:62px">
    <div class="card-top" style="background:var(--yellow)">
      <svg width="30" height="30" viewBox="0 0 30 30"><circle cx="15" cy="15" r="13" fill="none" stroke="#fff" stroke-width="2.2" stroke-dasharray="6 2"/><path d="M9 15l4 4 8-8" fill="none" stroke="#fff" stroke-width="2.6"/></svg>
    </div>
    <h3>XPRESS SERVICES</h3>
    <p>There are many variations of passages of Lorem Ipsum available, but the majority have suffered alteration in some form, by injected humour, or randomised words which don't look even slightly.</p>
    <div class="card-more"><svg width="9" height="9" viewBox="0 0 9 9"><path d="M2 1v6h6" fill="none" stroke="#fff" stroke-width="1.2"/></svg></div>
  </article>
  <article class="abs card" style="left:221px">
    <div class="card-top" style="background:var(--teal)">
      <svg width="36" height="24" viewBox="0 0 36 24" fill="#fff"><path d="M2 6l8-4 6 3 6-3 12 4v8l-8 8-6-4-6 4-12-10z"/></svg>
    </div>
    <h3>SIGNATURE FACIAL</h3>
    <p>There are many variations of passages of Lorem Ipsum available, but the majority have suffered alteration in some form, by injected humour, or randomised words which don't look even slightly.</p>
    <div class="card-more on"><svg width="9" height="9" viewBox="0 0 9 9"><path d="M2 1v6h6" fill="none" stroke="#fff" stroke-width="1.2"/></svg></div>
  </article>
  <article class="abs card" style="left:379px">
    <div class="card-top" style="background:var(--pink)">
      <svg width="32" height="32" viewBox="0 0 32 32"><circle cx="16" cy="16" r="14" fill="#fff"/><circle cx="16" cy="16" r="9.5" fill="none" stroke="#d6679a" stroke-width="2"/><path d="M11.5 16l3 3 6-6" fill="none" stroke="#d6679a" stroke-width="2.4"/></svg>
    </div>
    <h3>CHEMICAL PEEL</h3>
    <p>There are many variations of passages of Lorem Ipsum available, but the majority have suffered alteration in some form, by injected humour, or randomised words which don't look even slightly.</p>
    <div class="card-more"><svg width="9" height="9" viewBox="0 0 9 9"><path d="M2 1v6h6" fill="none" stroke="#fff" stroke-width="1.2"/></svg></div>
  </article>
  <article class="abs card" style="left:538px">
    <div class="card-top" style="background:var(--sage)">
      <svg width="32" height="32" viewBox="0 0 32 32" fill="#fff"><circle cx="11" cy="11" r="8"/><circle cx="23" cy="19" r="6"/><circle cx="13" cy="25" r="4.5"/><circle cx="11" cy="11" r="3" fill="#b2cb78"/><circle cx="23" cy="19" r="2.2" fill="#b2cb78"/><circle cx="13" cy="25" r="1.6" fill="#b2cb78"/></svg>
    </div>
    <h3>XPRESS MANICURE</h3>
    <p>There are many variations of passages of Lorem Ipsum available, but the majority have suffered alteration in some form, by injected humour, or randomised words which don't look even slightly.</p>
    <div class="card-more"><svg width="9" height="9" viewBox="0 0 9 9"><path d="M2 1v6h6" fill="none" stroke="#fff" stroke-width="1.2"/></svg></div>
  </article>
  <div class="abs btn view">VIEW MORE SERVICES</div>
</section>

<section>
  <div class="abs mission-photo" role="img" aria-label="Photo of folded hands with patterned nail art"></div>
  <div class="abs mission">
    <h2>OUR MISSION</h2>
    <p>To be the #1 nail and wax salon in the Brookhaven, CT area, offering the most meticulous manicures, pedicures, and waxing service. We use superior products, advanced techniques, and exceptional sanitation procedures to provide our clients with safe, quality services. Our knowledgeable and friendly staff is always happy to assist with any of your Polish &amp; Glow concerns.</p>
    <p>We are excited to welcome another Licensed Nail Technician to our team, Dana Whitfield. Dana has over 25 years experience and is also a certified Medical Nail Technician. You will love her spunk and genuine friendliness. If you're seeking a perfect mani, Dana is your girl.</p>
  </div>
  <div class="abs btn readmore">READ MORER</div>
</section>

<footer>
  <div class="abs footer"></div>
  <div class="abs zigzag"></div>
  <div class="abs fcol" style="left:63px">
    <h4>Our Link</h4>
    <ul><li class="go">Home</li><li class="go">Schedule AnAppointment</li><li class="go">Products and Services</li><li class="go">Careers</li><li class="go">Specials</li><li class="go">FUQ</li></ul>
  </div>
  <div class="abs fcol" style="left:225px">
    <h4>The Services</h4>
    <ul><li>Signature Manicure- $24</li><li>Gel Polish Manicure - $34</li><li>Signature Pedicure - $40</li><li>Brow Design - $13</li><li>Chin - $10</li><li>Brazilian $55</li></ul>
  </div>
  <div class="abs fcol" style="left:391px">
    <h4>Information</h4>
    <ul><li class="go">About US</li><li class="go">New Collection</li><li class="go">Best Sellers</li><li class="go">Manufacturers</li><li class="go">Privacy Policy</li><li class="go">Ters &amp; condition</li></ul>
  </div>
  <div class="abs fcol news" style="left:560px">
    <h4>Newsletter</h4>
    <p>Duis aute irure dolor in reprehenderit in voluptate velit esse cillum dolore.</p>
    <div class="email">Your email address</div>
  </div>
  <div class="abs btn subscribe">SUBSCRIBE</div>
  <div class="abs copy">@ 2016 www.thepolishandglowstudio.example - All Rights Reserved,</div>
</footer>

</body>
</html>
```